Help design website for "Brightwater Civic Advisors" to advance the common good

Here is the Google doc link that lays out the design:

https://files.plumrivet.example/sheet/d/7QmTzR2wLx9KpVbN4hJcY8sEaUoFdG3iXkMnPq5rWt6/edit?usp=sharing

Here is the Google drive folder with the logos and photos: https://vault.plumrivet.example/open?id=4HkWp9LzQe2TxRvN8mBaYc3DsUoJfG6

The testimonials are being gathered and will be shared by Friday, 1/4.

The winner will also have to migrate the coding files to my hosting site.

Thank you for your help! Looking forward to seeing your designs.

Target Market(s)

Prospective clients

Industry/Entity Type

Non Profit

Coding

Coded - Design and coding required

Number of Pages Required

5+ page

Requirements
Must have
• Noted in the Google doc regarding layout.
Nice to have

```html
<!DOCTYPE html>
<html lang="en">
<head>
<meta charset="utf-8">
<title>Brightwater Civic Advisors</title>
<link href="https://fonts.googleapis.com/css2?family=Lato:wght@300;400;700;900&display=swap" rel="stylesheet">
<style>
:root{
  --blue:#3a86cc;
  --blue-dark:#2f73b5;
  --navy:#0f2d52;
  --navy-deep:#0a2243;
  --ink:#222;
  --body:#444;
  --grey-bg:#e6e6e6;
  --white:#fff;
}
*{box-sizing:border-box;margin:0;padding:0}
html,body{width:1200px;height:3586px;overflow:hidden}
body{font-family:'Lato',sans-serif;color:var(--ink);background:var(--white);position:relative}
.abs{position:absolute}

/* Header */
.site-header{position:absolute;top:0;left:0;width:1200px;height:95px;background:var(--white)}
.main-nav{position:absolute;left:186px;top:36px;display:flex;gap:0}
.main-nav a{font-size:16px;font-weight:700;color:var(--ink);text-decoration:none;margin-right:48px;letter-spacing:.2px}
.brand{position:absolute;left:836px;top:22px;display:flex;align-items:center;gap:14px}
.brand-square{width:44px;height:44px;background:var(--blue)}
.brand-name{font-size:19px;font-weight:700;letter-spacing:3px;color:var(--navy);line-height:1.15;text-transform:uppercase}

/* Hero */
.hero{position:absolute;top:95px;left:0;width:1200px;height:555px;background:linear-gradient(180deg,#5b5048 0%,#3d3a3c 45%,#2b2d33 100%)}
.hero-title{position:absolute;top:170px;width:100%;text-align:center;color:var(--white)}
.hero-title .kicker{display:block;font-size:44px;font-weight:300;letter-spacing:5px}
.hero-title .name{display:block;font-size:66px;font-weight:900;line-height:1;letter-spacing:-1px}
.slide-arrow{position:absolute;top:218px;width:56px;height:56px;border-radius:50%;display:flex;align-items:center;justify-content:center}
.slide-arrow.prev{left:113px;background:var(--white)}
.slide-arrow.next{left:1033px;background:var(--blue)}

.notch{position:absolute;left:540px;width:120px;height:70px}

/* About */
.about-photo{position:absolute;left:168px;top:730px;width:372px;height:422px}
.about-copy{position:absolute;left:578px;top:752px;width:470px}
.section-title{font-size:33px;font-weight:700;color:var(--blue)}
.about-copy p{font-size:15px;line-height:1.55;color:var(--body);margin-top:18px}
.btn-outline{display:inline-block;border:3px solid var(--blue);color:var(--blue);font-weight:700;font-size:18px;text-align:center}
.about-copy .btn-outline{margin-top:30px;width:180px;height:50px;line-height:44px}

/* Services */
.services{position:absolute;top:1207px;left:0;width:1200px;height:557px;background:var(--blue)}
.services .section-title{color:var(--white);text-align:center;margin-top:48px;font-size:29px}
.service-card{position:absolute;top:167px;width:275px;height:301px;border:2px solid var(--white);color:var(--white);text-align:center;padding:88px 24px 0}
.service-card h3{font-size:20px;font-weight:700;line-height:1.15}
.service-card p{font-size:13px;line-height:1.6;margin-top:10px}
.service-card .btn-fill{position:absolute;left:67px;bottom:36px;width:140px;height:38px;line-height:38px;background:var(--white);color:var(--blue);font-size:14px;font-weight:700}
.service-icon{position:absolute;left:77px;top:-62px;width:120px;height:104px}
.svc-arrow{position:absolute;top:305px}

/* Testimonials */
.testimonials{position:absolute;top:1764px;left:0;width:1200px;height:363px;text-align:center}
.testimonials h2{font-size:25px;font-weight:700;color:#333;margin-top:76px}
.quote-mark{font-size:70px;font-weight:900;color:var(--blue);line-height:1;height:50px;margin-top:4px}
.testimonials blockquote{font-size:19px;color:#555;line-height:1.6;width:860px;margin:8px auto 0}
.testimonials .author{font-size:16px;font-weight:700;color:var(--blue);margin-top:28px}

/* Media */
.media{position:absolute;top:2127px;left:0;width:1200px;height:700px;background:linear-gradient(180deg,var(--grey-bg) 0%,#f4f4f4 60%,#fff 100%)}
.media .section-title{text-align:center;margin-top:78px;font-size:29px}
.media-card{position:absolute;top:139px;width:428px;height:404px;background:var(--white);box-shadow:0 2px 6px rgba(0,0,0,.18)}
.media-card .thumb{height:220px}
.media-card .body{padding:22px 30px 0}
.media-card h3{font-size:20px;font-weight:700;color:var(--blue);line-height:1.2}
.media-card p{font-size:14px;color:#888;line-height:1.5;margin-top:8px}
.media-card .more{font-size:14px;font-weight:700;color:var(--navy);margin-top:14px}
.media .btn-outline{position:absolute;left:507px;top:590px;width:180px;height:48px;line-height:42px;font-size:18px}

/* Consultation */
.consult{position:absolute;top:2827px;left:0;width:1200px;height:579px;background:linear-gradient(180deg,#163a66 0%,var(--navy) 55%,var(--navy-deep) 100%)}
.consult h2{color:var(--white);text-align:center;font-size:32px;font-weight:700;line-height:1.1;margin-top:66px}
.field{position:absolute;width:419px;height:50px;border:1.5px solid rgba(255,255,255,.75);color:var(--white);font-size:14px;padding:14px 20px;letter-spacing:.5px}
.field.message{height:180px;width:416px}
.submit{position:absolute;left:507px;top:438px;width:179px;height:48px;background:var(--blue);color:var(--white);font-size:18px;font-weight:700;text-align:center;line-height:48px;box-shadow:0 2px 4px rgba(0,0,0,.3)}

/* Footer */
.site-footer{position:absolute;top:3406px;left:0;width:1200px;height:180px;text-align:center}
.footer-nav{margin-top:50px}
.footer-nav a{font-size:14px;font-weight:700;color:var(--blue);text-decoration:none;margin:0 20px}
.copyright{font-size:13px;color:#555;margin-top:12px}
.social{display:flex;justify-content:center;gap:8px;margin-top:18px}
.social span{width:29px;height:29px;border:2px solid var(--blue);border-radius:50%}
</style>
</head>
<body>

<header class="site-header">
  <nav class="main-nav">
    <a href="#">ABOUT</a>
    <a href="#">SERVICES &amp; TESTIMONIALS</a>
    <a href="#">MEDIA &amp; IMPACT</a>
    <a href="#">CONTACT</a>
  </nav>
  <div class="brand">
    <span class="brand-square"></span>
    <span class="brand-name">Brightwater<br>Civic Advisors</span>
  </div>
</header>

<section class="hero" role="img" aria-label="Photo of an audience seated in an art gallery listening to a speaker">
  <h1 class="hero-title"><span class="kicker">WELCOME TO</span><span class="name">BRIGHTWATER<br>CIVIC ADVISORS</span></h1>
  <div class="slide-arrow prev"><svg width="20" height="20" viewBox="0 0 20 20"><path d="M13 3 L6 10 L13 17" fill="none" stroke="#3a86cc" stroke-width="3"/></svg></div>
  <div class="slide-arrow next"><svg width="20" height="20" viewBox="0 0 20 20"><path d="M7 3 L14 10 L7 17" fill="none" stroke="#fff" stroke-width="3"/></svg></div>
</section>

<svg class="notch" style="top:596px" viewBox="0 0 120 70"><path d="M0 54 L60 0 L120 54 L120 70 L0 70Z" fill="#fff"/></svg>

<svg class="about-photo" viewBox="0 0 372 422" role="img" aria-label="Portrait photo of the founder">
  <polygon points="186,2 370,107 370,315 186,420 2,315 2,107" fill="none" stroke="#3a86cc" stroke-width="2"/>
  <defs><linearGradient id="portrait" x1="0" y1="0" x2="0" y2="1"><stop offset="0" stop-color="#6a6a6a"/><stop offset="1" stop-color="#2c2c2c"/></linearGradient></defs>
  <polygon points="186,24 350,118 350,304 186,398 22,304 22,118" fill="url(#portrait)"/>
</svg>

<section class="about-copy">
  <h2 class="section-title">ABOUT US</h2>
  <p>Brightwater Civic Advisors supports nonprofit organizations and educational institutions to carry out their missions to benefit the wider community.</p>
  <p>Founder Mara Linden is an educator with a 22-year record of demonstrated achievement and leadership roles in nonprofits and educational institutions. Most recently, she served as Associate Dean of Students in the University and Director of the University Community Service Center at Lakeshore University.</p>
  <a class="btn-outline">READ MORE</a>
</section>

<section class="services">
  <svg class="notch" style="top:-32px;left:555px;width:90px;height:60px" viewBox="0 0 90 60"><path d="M0 0 L90 0 L90 30 L45 60 L0 30Z" fill="#fff"/></svg>
  <h2 class="section-title">OUR SERVICES</h2>

  <svg class="svc-arrow" style="left:92px" width="42" height="24" viewBox="0 0 42 24"><path d="M40 12 H4 M14 2 L3 12 L14 22" fill="none" stroke="#fff" stroke-width="3"/></svg>
  <svg class="svc-arrow" style="left:1066px" width="42" height="24" viewBox="0 0 42 24"><path d="M2 12 H38 M28 2 L39 12 L28 22" fill="none" stroke="#fff" stroke-width="3"/></svg>

  <div class="service-card" style="left:162px">
    <svg class="service-icon" viewBox="0 0 120 104"><polygon points="30,2 90,2 118,52 90,102 30,102 2,52" fill="#3a86cc" stroke="#fff" stroke-width="2"/><g fill="none" stroke="#fff" stroke-width="2"><circle cx="60" cy="34" r="6"/><circle cx="44" cy="48" r="5"/><circle cx="76" cy="48" r="5"/><path d="M36 74 V62 h16 v12 M68 74 V62 h16 v12 M52 74 V46 h16 v28"/></g></svg>
    <h3>Group Facilitation &amp; Leadership Training</h3>
    <p>Mara has facilitated student groups, experiential learning activities, and dialogues on social justice issue</p>
    <span class="btn-fill">READ MORE</span>
  </div>
  <div class="service-card" style="left:463px">
    <svg class="service-icon" viewBox="0 0 120 104"><polygon points="30,2 90,2 118,52 90,102 30,102 2,52" fill="#3a86cc" stroke="#fff" stroke-width="2"/><g fill="none" stroke="#fff" stroke-width="2"><rect x="34" y="32" width="52" height="34"/><path d="M52 78 h16 M60 66 v12"/><circle cx="60" cy="49" r="8"/><circle cx="60" cy="49" r="3"/></g></svg>
    <h3>Program Design, Implementation, &amp; Evaluation</h3>
    <p>Mara has launched several programs that take into account</p>
    <span class="btn-fill">READ MORE</span>
  </div>
  <div class="service-card" style="left:765px">
    <svg class="service-icon" viewBox="0 0 120 104"><polygon points="30,2 90,2 118,52 90,102 30,102 2,52" fill="#3a86cc" stroke="#fff" stroke-width="2"/><g fill="none" stroke="#fff" stroke-width="2"><path d="M40 30 h16 v8 a5 5 0 0 0 8 0 v-8 h16 v16 h-8 a5 5 0 0 0 0 8 h8 v20 h-40 Z"/></g></svg>
    <h3>Strategic Planning &amp; Visioning</h3>
    <p>At Lakeshore University, Mara established and managed a 16-member Advisory Board</p>
    <span class="btn-fill">READ MORE</span>
  </div>
</section>

<section class="testimonials">
  <h2>TESTIMONIALS</h2>
  <div class="quote-mark">&ldquo;</div>
  <blockquote>Renata Villar, Assistant Clinical Professor, Clerkship Director, Department of Family Medicine, Lakeshore University Biological Sciences</blockquote>
  <div class="author">BY AUTHOR NAME</div>
</section>

<section class="media">
  <svg class="notch" style="top:-24px;left:555px;width:90px;height:70px" viewBox="0 0 90 70"><path d="M0 24 L90 24 L90 50 L45 70 L0 50Z" fill="#fff"/></svg>
  <h2 class="section-title">MEDIA &amp; IMPACT</h2>
  <article class="media-card" style="left:158px">
    <div class="thumb" role="img" aria-label="Photo of attendees listening to a speaker in a gym hall" style="background:linear-gradient(180deg,#8a8a86,#4d5a4a)"></div>
    <div class="body">
      <h3>Attendees listening to a speaker at the Common Ground Dinner Dialogue event</h3>
      <p>Lorem ipsum dolor sit amet consectetuer adipiscing elit Nam cursus Morbi ut mi Nullam enim leo</p>
      <div class="more">READ MORE</div>
    </div>
  </article>
  <article class="media-card" style="left:598px">
    <div class="thumb" role="img" aria-label="Photo of students touring a rooftop garden among city buildings" style="background:linear-gradient(180deg,#9ea3a6,#5c6b4e)"></div>
    <div class="body">
      <h3>Students at Riverton City Hall's Rooftop Garden</h3>
      <p>Lorem ipsum dolor sit amet consectetuer adipiscing elit Nam cursus Morbi ut mi Nullam enim leo</p>
      <div class="more">READ MORE</div>
    </div>
  </article>
  <a class="btn-outline">VIEW MORE</a>
</section>

<section class="consult" aria-label="Consultation form over a faded audience photo">
  <h2>BOOK A COMPLIMENTARY<br>CONSULTATION</h2>
  <div class="field" style="left:179px;top:170px">FIRST NAME</div>
  <div class="field" style="left:179px;top:234px">ORGANIZATION NAME</div>
  <div class="field" style="left:179px;top:297px">EMAIL ADDRESS</div>
  <div class="field" style="left:179px;top:361px">SUBJECT</div>
  <div class="field" style="left:612px;top:170px;width:416px">LAST NAME</div>
  <div class="field message" style="left:612px;top:234px">MESSAGE</div>
  <div class="submit">SUBMIT</div>
</section>

<footer class="site-footer">
  <svg class="notch" style="top:-36px;left:555px;width:90px;height:60px" viewBox="0 0 90 60"><path d="M0 36 L45 4 L90 36 L90 60 L0 60Z" fill="#fff"/></svg>
  <nav class="footer-nav">
    <a href="#">ABOUT</a><a href="#">SERVICES &amp; TESTIMONIALS</a><a href="#">MEDIA &amp; IMPACT</a><a href="#">CONTACT</a>
  </nav>
  <div class="copyright">© 2019 Company Name &nbsp;All right reserved</div>
  <div class="social"><span></span><span></span><span></span></div>
</footer>

</body>
</html>
```